Business Card Design

We are a manufacturing and distribution company with most of our customer base being supermarkets. We have established brand guidelines that are attached.

```html
<!DOCTYPE html>
<html lang="en">
<head>
<meta charset="utf-8">
<title>Voraline Business Card</title>
<link rel="stylesheet" href="https://fonts.googleapis.com/css2?family=Montserrat:wght@700;800&family=Arimo:wght@400;700&display=swap">
<style>
  :root{
    --bg:#e4e4e2;
    --blue:#0268ad;
    --blue-light:#2c96d8;
    --charcoal:#2a292a;
    --charcoal-light:#3c3b3c;
    --red:#e0201f;
    --white:#ffffff;
  }
  *{margin:0;padding:0;box-sizing:border-box}
  html,body{width:1200px;height:802px;overflow:hidden;background:var(--bg)}
  .stage{position:relative;width:1200px;height:802px}
  .card{
    position:absolute;top:252px;width:520px;height:297px;
    background:var(--blue);overflow:hidden;
    border:2px solid var(--red);
    box-shadow:0 6px 18px rgba(0,0,0,.18);
  }
  .card--front{left:52px}
  .card--back{left:628px}
  .card svg{position:absolute;left:0;top:0}
  .brand{
    position:absolute;font-family:"Montserrat",sans-serif;font-weight:800;
    color:var(--white);letter-spacing:1.5px;line-height:1;white-space:nowrap;
  }
  .brand--panel{left:78px;top:136px;font-size:26px}
  .brand-square{position:absolute;left:52px;top:140px;width:18px;height:18px;background:var(--blue-light)}
  .brand--top{right:28px;top:30px;font-size:24px}
  .brand--back{right:40px;top:126px;font-size:34px;font-weight:700;letter-spacing:2px}
  .details{
    position:absolute;right:28px;top:82px;text-align:right;
    font-family:"Arimo",sans-serif;color:var(--white);
  }
  .person-name{font-weight:700;font-size:13px;letter-spacing:.5px;text-transform:uppercase}
  .person-role{font-size:11px;margin-top:2px}
  .address{font-size:11px;line-height:1.35;margin-top:14px}
  .contacts{list-style:none;font-size:11px;line-height:1.5;margin-top:12px}
  .contacts li{display:flex;justify-content:flex-end;align-items:center;gap:6px}
  .contacts svg{position:static;width:10px;height:10px}
</style>
</head>
<body>
<main class="stage">

  <section class="card card--front">
    <svg width="520" height="297" viewBox="0 0 520 297" role="img" aria-label="Dark angled panel with faint large brand decoration">
      <defs>
        <linearGradient id="panelShade" x1="0" y1="0" x2="1" y2="1">
          <stop offset="0" stop-color="var(--charcoal-light)"/>
          <stop offset="1" stop-color="var(--charcoal)"/>
        </linearGradient>
      </defs>
      <path d="M-4 -4 L94 -4 L322 128 Q336 137 328 150 L114 301 L-4 301 Z"
            fill="url(#panelShade)" stroke="var(--red)" stroke-width="2"/>
    </svg>
    <span class="brand-square"></span>
    <div class="brand brand--panel">VORALINE</div>

    <div class="brand brand--top">VORALINE</div>
    <div class="details">
      <p class="person-name">Marcus Ellory</p>
      <p class="person-role">Manager</p>
      <p class="address">Your address, city<br>state, ZIP 0000</p>
      <ul class="contacts">
        <li>123-456-2100
          <svg viewBox="0 0 10 10"><path d="M2 1 L4 1 L4.5 3 L3.5 4 Q4.5 6 6 6.5 L7 5.5 L9 6 L9 8 Q5 9 1.5 4.5 Q1 2.5 2 1Z" fill="var(--white)"/></svg>
        </li>
        <li>youremail@example.com
          <svg viewBox="0 0 10 10"><rect x="1" y="2.5" width="8" height="5.5" fill="none" stroke="var(--white)" stroke-width="1"/><path d="M1 2.5 L5 6 L9 2.5" fill="none" stroke="var(--white)" stroke-width="1"/></svg>
        </li>
        <li>www.yourwebsite.com
          <svg viewBox="0 0 10 10"><circle cx="5" cy="5" r="4" fill="none" stroke="var(--white)" stroke-width="1"/><path d="M1 5 H9 M5 1 Q2.5 5 5 9 Q7.5 5 5 1" fill="none" stroke="var(--white)" stroke-width=".8"/></svg>
        </li>
      </ul>
    </div>
  </section>

  <section class="card card--back">
    <svg width="520" height="297" viewBox="0 0 520 297" role="img" aria-label="Large faint brand decoration on the left side">
      <defs>
        <linearGradient id="backGlow" x1="0" y1="1" x2="1" y2="0">
          <stop offset="0" stop-color="var(--blue-light)"/>
          <stop offset="1" stop-color="var(--blue)" stop-opacity="0"/>
        </linearGradient>
      </defs>
      <rect x="0" y="0" width="250" height="297" fill="url(#backGlow)"/>
    </svg>
    <div class="brand brand--back">VORALINE</div>
  </section>

</main>
</body>
</html>
```